business card deign

Logo needs the following on it.
1. attached logo
2. Tagline - "If it keeps a drink cold or the party going...we do it!"
3. Name- Dalton Pikes, Founder and CPO
4. Address - 412 E. Carver Avenue, Ste 2207, Tampa, FL. 33917
5. Phone - 555.318.4726

```html
<!DOCTYPE html>
<html lang="en">
<head>
<meta charset="utf-8">
<title>Kelvora Business Card</title>
<link href="https://fonts.googleapis.com/css2?family=Roboto:wght@400;700&display=swap" rel="stylesheet">
<style>
  :root {
    --stage: #222222;
    --card-dark: #141414;
    --card-black: #0c0c0c;
    --paper: #ffffff;
    --ink: #111111;
    --text-light: #f2f2f2;
  }
  * { margin: 0; padding: 0; box-sizing: border-box; }
  html, body {
    width: 1200px; height: 711px; overflow: hidden;
    background: var(--stage);
    font-family: "Roboto", Arial, sans-serif;
  }
  .stage {
    position: relative; width: 1200px; height: 711px;
    display: flex; align-items: center; justify-content: center; gap: 50px;
  }
  .card {
    position: relative; width: 525px; height: 300px;
    border-radius: 4px; overflow: hidden;
    box-shadow: 0 14px 30px rgba(0,0,0,.55);
  }
  .card-front { background: var(--card-black); display: flex; align-items: center; justify-content: center; }
  .brand {
    display: flex; align-items: center; gap: 14px;
    font-weight: 700; letter-spacing: .32em; font-size: 38px; white-space: nowrap;
  }
  .brand-dot { width: 22px; height: 22px; border-radius: 50%; flex: none; }
  .card-front .brand { color: var(--paper); }
  .card-front .brand-dot { background: var(--paper); }

  .card-back { background: var(--card-dark); }
  .back-ring {
    position: absolute; left: 262px; top: -42px; width: 384px; height: 384px;
    border-radius: 50%; border: 3px solid var(--paper);
  }
  .back-disc {
    position: absolute; left: 274px; top: -46px; width: 392px; height: 392px;
    border-radius: 50%; background: var(--paper);
  }
  .back-brand {
    position: absolute; left: 318px; top: 50%; transform: translateY(-50%);
    color: var(--ink); font-size: 22px; gap: 10px; letter-spacing: .28em;
  }
  .back-brand .brand-dot { background: var(--ink); width: 14px; height: 14px; }

  .identity { position: absolute; left: 20px; top: 36px; display: flex; gap: 10px; }
  .identity-bar { width: 10px; height: 52px; background: var(--paper); }
  .person-name { color: var(--text-light); font-weight: 700; font-size: 25px; line-height: 1.1; }
  .person-role { color: var(--text-light); font-size: 14px; margin-top: 4px; }

  .details { position: absolute; left: 30px; bottom: 34px; color: var(--text-light); font-size: 12.5px; line-height: 1.45; }
  .tagline { margin-bottom: 12px; }
  .contact-row { display: flex; gap: 8px; align-items: flex-start; }
  .contact-row svg { width: 12px; height: 12px; margin-top: 3px; flex: none; }
</style>
</head>
<body>
<main class="stage">
  <section class="card card-front">
    <div class="brand"><span class="brand-dot"></span>KELVORA</div>
  </section>

  <section class="card card-back">
    <div class="back-ring"></div>
    <div class="back-disc"></div>
    <div class="brand back-brand"><span class="brand-dot"></span>KELVORA</div>

    <div class="identity">
      <div class="identity-bar"></div>
      <div>
        <div class="person-name">Dalton Pikes</div>
        <div class="person-role">Founder and CPO</div>
      </div>
    </div>

    <div class="details">
      <p class="tagline">If it keeps a drink cold or<br>the party going...we do it!</p>
      <div class="contact-row">
        <svg viewBox="0 0 24 24" fill="#f2f2f2"><path d="M6.6 10.8a15 15 0 0 0 6.6 6.6l2.2-2.2a1 1 0 0 1 1-.25 11.4 11.4 0 0 0 3.6.6 1 1 0 0 1 1 1V20a1 1 0 0 1-1 1A17 17 0 0 1 3 4a1 1 0 0 1 1-1h3.5a1 1 0 0 1 1 1c0 1.25.2 2.45.6 3.6a1 1 0 0 1-.25 1z"/></svg>
        <span>555.318.4726</span>
      </div>
      <div class="contact-row">
        <svg viewBox="0 0 24 24" fill="none" stroke="#f2f2f2" stroke-width="2.4"><path d="M12 22s7-7 7-12a7 7 0 0 0-14 0c0 5 7 12 7 12z"/><circle cx="12" cy="10" r="2.5"/></svg>
        <span>412 E. Carver Avenue,<br>Ste 2207, Tampa, FL. 33917</span>
      </div>
    </div>
  </section>
</main>
</body>
</html>
```